Local Roofing/Construction company business needs new biz card design

We need a new business card design, current cards are from the start of this operation and generic at best. We are a local Construction Company (General Contractor) with a majority of our work originating from insurance claims-exterior finish work is the main focus (Roofs-Siding-Gutters etc). Heavily involved with homeowners and the low ball offers they receive from insurance company's after a insurable event takes place. I have attached some of our original logo file(s) below.

```html
<!DOCTYPE html>
<html lang="en">
<head>
<meta charset="UTF-8">
<title>Ridgeline Construction – Business Card</title>
<link rel="stylesheet" href="https://fonts.googleapis.com/css2?family=Exo+2:wght@700&family=Arimo:wght@400&display=swap">
<style>
  :root {
    --page-bg: #e9e7e6;
    --card-light: #f4f2f1;
    --card-dark: #0e1f22;
    --accent-green: #22d46b;
    --text-white: #ffffff;
    --divider: #ffffff;
  }
  * { margin: 0; padding: 0; box-sizing: border-box; }
  html, body {
    width: 1200px;
    height: 900px;
    overflow: hidden;
    background: var(--page-bg);
  }
  .canvas {
    width: 1200px;
    height: 900px;
    display: flex;
    align-items: center;
    justify-content: center;
  }
  .business-card {
    width: 1000px;
    height: 617px;
    display: flex;
    flex-direction: column;
    box-shadow: 0 14px 40px rgba(0,0,0,0.18);
  }
  .card-top {
    height: 335px;
    background: var(--card-light);
    display: flex;
    align-items: center;
    justify-content: center;
    gap: 22px;
  }
  .brand-square {
    width: 64px;
    height: 64px;
    background: var(--accent-green);
  }
  .brand-name {
    font-family: "Exo 2", sans-serif;
    font-weight: 700;
    font-size: 60px;
    letter-spacing: 1px;
    color: var(--card-dark);
    text-transform: uppercase;
  }
  .accent-rule {
    height: 7px;
    background: var(--accent-green);
  }
  .card-bottom {
    flex: 1;
    background: var(--card-dark);
    position: relative;
    color: var(--text-white);
    font-family: "Arimo", sans-serif;
  }
  .identity {
    position: absolute;
    right: 547px;
    top: 82px;
    text-align: right;
  }
  .person-name {
    font-family: "Exo 2", sans-serif;
    font-weight: 700;
    font-size: 38px;
    color: var(--accent-green);
    letter-spacing: 0.5px;
    line-height: 1.1;
    text-transform: uppercase;
  }
  .person-role {
    font-size: 28px;
    line-height: 1.25;
  }
  .divider {
    position: absolute;
    left: 493px;
    top: 75px;
    width: 2px;
    height: 95px;
    background: var(--divider);
  }
  .contact-list {
    position: absolute;
    left: 521px;
    top: 69px;
    list-style: none;
  }
  .contact-item {
    display: flex;
    align-items: center;
    gap: 8px;
    font-size: 28px;
    height: 37px;
  }
  .contact-icon {
    width: 27px;
    height: 27px;
    flex: none;
  }
  .address {
    position: absolute;
    left: 0;
    right: 0;
    top: 200px;
    text-align: center;
    font-size: 27px;
  }
</style>
</head>
<body>
  <main class="canvas">
    <article class="business-card">
      <header class="card-top">
        <span class="brand-square"></span>
        <span class="brand-name">Ridgeline Construction</span>
      </header>
      <div class="accent-rule"></div>
      <section class="card-bottom">
        <div class="identity">
          <p class="person-name">Daniel Reeves</p>
          <p class="person-role">Managing Director</p>
        </div>
        <div class="divider"></div>
        <ul class="contact-list">
          <li class="contact-item">
            <svg class="contact-icon" viewBox="0 0 24 24" aria-hidden="true">
              <path fill="#22d46b" d="M6.6 10.8a15.1 15.1 0 0 0 6.6 6.6l2.2-2.2c.3-.3.7-.4 1-.2 1.1.4 2.3.6 3.6.6.6 0 1 .4 1 1V20c0 .6-.4 1-1 1A17 17 0 0 1 3 4c0-.6.4-1 1-1h3.5c.6 0 1 .4 1 1 0 1.3.2 2.5.6 3.6.1.3 0 .7-.2 1l-2.3 2.2z"/>
              <path fill="none" stroke="#22d46b" stroke-width="1.8" stroke-linecap="round" d="M14 2.5a8 8 0 0 1 7.5 7.5M14 6a4.5 4.5 0 0 1 4 4"/>
            </svg>
            <span>044-123 456 789</span>
          </li>
          <li class="contact-item">
            <svg class="contact-icon" viewBox="0 0 24 24" aria-hidden="true">
              <rect x="1.5" y="5" width="21" height="14" fill="#22d46b"/>
              <path fill="none" stroke="#0e1f22" stroke-width="1.6" d="M1.5 5 12 13 22.5 5M1.5 19l8-7M22.5 19l-8-7"/>
            </svg>
            <span>info@webname.com</span>
          </li>
          <li class="contact-item">
            <svg class="contact-icon" viewBox="0 0 24 24" aria-hidden="true">
              <g fill="none" stroke="#22d46b" stroke-width="1.8">
                <circle cx="12" cy="12" r="10"/>
                <ellipse cx="12" cy="12" rx="4.5" ry="10"/>
                <path d="M2 12h20M3.5 7h17M3.5 17h17"/>
              </g>
            </svg>
            <span>www.websitename.com</span>
          </li>
        </ul>
        <p class="address">421, Address line goes here 45452,Country Name</p>
      </section>
    </article>
  </main>
</body>
</html>
```